Stationery Design Project

We need a stationery design for our Norwegian trucking company. We have existed for about 15 years and our 12 drivers uses relatively new vehicles to transport goods around in northern Norway. Long distance routes with fresh fish og food transport is our main operations.

We have already made alogo that's printed on our trucks. The logo and a picture of our trucks is attached. I think the logo i crappy, but since its already in use, changing it is not an option in this round. Still using a better colour scheme in the overall stationery and more interesting fonts is possible (altso in the logo).

Company details:
Name: Kjelvraket AS
Organisation nr 873 615 309
Post adress: 8642 Raudvik

I like minimalism and simplicity. I am avalibly for questions in normal GMT working hours either here or on mail: ivar@fjordlast.no

Reason: Hi. Im extending the deadline because I needed some time to find a vector file of our logo. Sorry for the inconvenience

Hi, and thanks for all your interest in the project. Some updates:

-          I have decided to commit to using one of the designs. Some designer will get the payment.

-          I have extended the deadline with 24 hours since I needed some time to find our firms vector logo (a slow Swedish man was holding me up)

-          We will not choose a design before the deadline. No need to rush.

-          We have received a lot of great design and think there is a need to specified the product we want to make:

o   Business Card for all our employers. I just need the design and will duplicate with the correct numbers and name myself. The information on should be: Logo, employer’s name, Phone number, email, website, Postal number and address. Use this as a template: logo, Leif Brattvoll, 47382066, Leif@fjordlast.no,, fjordlast.no, 8642 Raudvik. The order and placement of the information is your creative decision.

o   Stickers to put on the goods we travel. On the sticker the should be the following information: Logo, phone number, Tekst and link: Fraktæ av Kjelvraket. Ke du syns? Fjordlast.no/tilbakemelding (this means: Handled by Kjelvraket. What do you think Fjordlast.no/feedback -à the link will be a feedback form). The placement the information and size is your creative decision with some stings: we have been thinking of using Drukko for printing and see that a size about 6x6 cm, 8x5 or something like that. (with 3000 copies our budget is 200 punds). Any suggestions of other suppliers are welcome. Drukko price calculator http://www.drukkolabelhouse.co.uk/digital-litho-printing/printing-labels-tags/stickers/

o   Letterhead with logo, address, phone number and organizational number.

o   Envelopes with logo,address, phone number and organizational number.

Have a nice day.

 

 

• Using the blue colour in the logo and using a similar graphic approch.

```html
<!DOCTYPE html>
<html lang="no">
<head>
<meta charset="utf-8">
<title>Kjelvraket AS – Stationery</title>
<link href="https://fonts.googleapis.com/css2?family=Open+Sans:wght@400;600;700&display=swap" rel="stylesheet">
<style>
  :root {
    --blue: #1f4fae;
    --blue-faint: #dbe4f3;
    --ink: #232326;
    --paper: #ffffff;
    --text: #3a3a3a;
    --muted: #6d6d6d;
    --rule: #8a8a8a;
    --stage: #2b2c30;
  }
  * { box-sizing: border-box; margin: 0; padding: 0; }
  html, body { width: 1200px; height: 665px; overflow: hidden; }
  body {
    background: var(--stage);
    font-family: "Open Sans", Arial, sans-serif;
    color: var(--text);
    position: relative;
  }
  .item { position: absolute; background: var(--paper); overflow: hidden; }
  .wave { position: absolute; left: 0; top: 0; width: 100%; display: block; }

  .brand {
    position: absolute; display: flex; align-items: center; gap: 5px;
    color: var(--blue); font-weight: 700; letter-spacing: -0.3px; white-space: nowrap;
  }
  .brand::before {
    content: ""; display: block; border-radius: 50%; background: var(--blue);
    width: .7em; height: .7em;
  }
  .brand--white { color: #fff; }
  .brand--white::before { background: #fff; }

  .head-meta {
    position: absolute; right: 14px; top: 18px; color: #fff;
    font-size: 7.5px; line-height: 11px; text-align: right;
  }
  .contact { position: absolute; font-size: 7px; line-height: 9px; color: var(--muted); }

  /* Fax */
  .fax { left: 27px; top: 25px; width: 342px; height: 442px; }
  .fax .brand { left: 22px; top: 43px; font-size: 21px; }
  .fax-title { position: absolute; left: 22px; top: 74px; font-size: 20px; font-weight: 400; color: #222; }
  .fax-fields { position: absolute; left: 22px; top: 104px; width: 292px; display: grid;
    grid-template-columns: 150px 136px; column-gap: 6px; row-gap: 9px; }
  .field { font-size: 7px; color: var(--text); border-bottom: 1px solid var(--rule); padding-bottom: 1px; }
  .fax-checks { position: absolute; left: 22px; top: 183px; display: flex; gap: 12px; font-size: 7px; }
  .check { display: flex; align-items: center; gap: 4px; }
  .check::before { content: ""; width: 7px; height: 7px; background: #c9c9c9; }
  .fax .contact, .letter .contact { left: 20px; top: 396px; }

  /* Letterhead */
  .letter { left: 409px; top: 25px; width: 342px; height: 442px; }
  .letter .brand { left: 22px; top: 43px; font-size: 21px; }
  .letter .brand--faint { left: 52px; top: 190px; font-size: 48px; color: var(--blue-faint); }
  .letter .brand--faint::before { background: var(--blue-faint); }

  /* Compliment slip */
  .slip { left: 794px; top: 28px; width: 382px; height: 165px; }
  .slip .brand { left: 14px; top: 45px; font-size: 21px; }
  .slip .contact { left: 13px; top: 114px; font-size: 7px; color: var(--text); }

  /* Envelope */
  .env-flap { position: absolute; left: 797px; top: 211px; width: 380px; height: 44px; }
  .env-flap .brand { left: 160px; top: 14px; font-size: 10px; transform: rotate(180deg); }
  .envelope { left: 797px; top: 271px; width: 382px; height: 211px; border-radius: 38px 38px 0 0; }
  .envelope .brand--flip { left: 160px; top: 14px; font-size: 10px; transform: rotate(180deg); }
  .envelope .wave { top: 44px; }
  .envelope .brand--main { left: 12px; top: 85px; font-size: 21px; }
  .envelope .contact { left: 14px; top: 123px; font-size: 7.5px; line-height: 10px; color: var(--text); }
  .env-web { position: absolute; left: 16px; top: 186px; font-size: 6.5px; letter-spacing: 3px; color: var(--muted); }

  /* Business cards */
  .card { top: 526px; width: 152px; height: 87px; border-radius: 7px; }
  .card--front { left: 31px; }
  .card--front .card-name { position: absolute; right: 8px; top: 6px; font-size: 5.5px; color: #fff; }
  .card--front .brand { left: 8px; top: 31px; font-size: 12px; }
  .card-addr { position: absolute; left: 9px; top: 65px; font-size: 4.5px; line-height: 6px; color: var(--muted); }
  .card-reach { position: absolute; right: 9px; top: 59px; font-size: 4.5px; line-height: 6px; color: var(--muted); }
  .card--back { left: 198px; }
  .card--back .brand, .card--dark .brand { left: 32px; top: 28px; font-size: 13px; }
  .card-web { position: absolute; left: 0; width: 100%; top: 75px; text-align: center;
    font-size: 4px; letter-spacing: 1.5px; color: var(--muted); }
  .card--dark { left: 366px; background: var(--ink); }
  .card--dark .card-web { color: #9a9a9a; }

  /* Stickers */
  .sticker-rect { left: 633px; top: 526px; width: 129px; height: 96px; border-radius: 7px; }
  .sticker-meta { position: absolute; right: 6px; top: 3px; color: #fff; font-size: 4.5px; line-height: 5.5px; text-align: right; }
  .sticker-rect .brand { left: 16px; top: 29px; font-size: 11px; }
  .sticker-text { position: absolute; left: 0; width: 100%; text-align: center; color: var(--blue); }
  .sticker-rect .sticker-text { top: 59px; font-size: 7.5px; line-height: 9px; }
  .sticker-round { left: 919px; top: 531px; width: 96px; height: 96px; border-radius: 50%; }
  .sticker-round .brand { left: 14px; top: 29px; font-size: 9.5px; }
  .sticker-round .sticker-text { top: 48px; font-size: 6px; line-height: 7px; color: var(--ink); }
  .sticker-small { position: absolute; left: 0; width: 100%; top: 73px; text-align: center; font-size: 3.5px; line-height: 4.5px; color: var(--muted); }
</style>
</head>
<body>

<svg width="0" height="0" style="position:absolute" aria-hidden="true">
  <symbol id="swoosh" viewBox="0 0 340 56" preserveAspectRatio="none">
    <path fill="var(--ink)" d="M0 10 C100 28 200 46 340 38 V45 C200 60 100 44 0 28 Z"/>
    <path fill="var(--blue)" d="M0 0 H340 V38 C200 46 100 24 0 12 Z"/>
  </symbol>
</svg>

<!-- Fax sheet -->
<section class="item fax">
  <svg class="wave" height="56"><use href="#swoosh"/></svg>
  <div class="head-meta">8642 Raudvik.<br>Org. nr. 873 615 309</div>
  <div class="brand">Kjelvraket</div>
  <h1 class="fax-title">FAX</h1>
  <div class="fax-fields">
    <div class="field">To :</div><div class="field">From :</div>
    <div class="field">Fax :</div><div class="field">Page:</div>
    <div class="field">Phone :</div><div class="field">Date:</div>
    <div class="field">Re :</div><div class="field">CC:</div>
  </div>
  <div class="fax-checks">
    <span class="check">Urgent</span>
    <span class="check">For Review</span>
    <span class="check">Please Comment</span>
    <span class="check">Please Reply</span>
    <span>Please Recycle</span>
  </div>
  <div class="contact">phone : 47382066<br>email : Leif@fjordlast.no<br>web : www.fjordlast.no</div>
</section>

<!-- Letterhead -->
<section class="item letter">
  <svg class="wave" height="56"><use href="#swoosh"/></svg>
  <div class="head-meta">8642 Raudvik.<br>Org. nr. 873 615 309</div>
  <div class="brand">Kjelvraket</div>
  <div class="brand brand--faint" aria-hidden="true">Kjelvraket</div>
  <div class="contact">phone : 47382066<br>email : Leif@fjordlast.no<br>web : www.fjordlast.no</div>
</section>

<!-- Compliment slip -->
<section class="item slip">
  <svg class="wave" height="52"><use href="#swoosh"/></svg>
  <div class="head-meta">8642 Raudvik.<br>Org. nr. 873 615 309</div>
  <div class="brand">Kjelvraket</div>
  <div class="contact">phone : 47382066<br>email : Leif@fjordlast.no<br>web : www.fjordlast.no<br>8642 Raudvik.<br>Org. nr. 873 615 309</div>
</section>

<!-- Envelope back flap -->
<svg class="env-flap" viewBox="0 0 380 44" aria-hidden="true">
  <path fill="var(--blue)" d="M10 0 H370 L380 44 H0 Z"/>
</svg>
<div class="env-flap" style="background:none"><div class="brand brand--white">Kjelvraket</div></div>

<!-- Envelope front -->
<section class="item envelope">
  <div class="brand brand--flip">Kjelvraket</div>
  <svg class="wave" height="62" viewBox="0 0 340 56" preserveAspectRatio="none">
    <path fill="var(--ink)" d="M0 22 C100 40 200 50 340 42 V48 C200 60 100 52 0 38 Z"/>
    <path fill="var(--blue)" d="M0 0 H340 V42 C200 48 100 36 0 24 Z"/>
  </svg>
  <div class="brand brand--main">Kjelvraket</div>
  <div class="contact">8642 Raudvik.<br>Org. nr. 873 615 309</div>
  <div class="env-web">www.fjordlast.no</div>
</section>

<!-- Business card front -->
<section class="item card card--front">
  <svg class="wave" height="26"><use href="#swoosh"/></svg>
  <div class="card-name">Leif Brattvoll</div>
  <div class="brand">Kjelvraket</div>
  <div class="card-addr">8642 Raudvik.<br>Organisation nr 873 615 309</div>
  <div class="card-reach">phone : 47382066<br>email : Leif@fjordlast.no<br>web : www.fjordlast.no</div>
</section>

<!-- Business card back -->
<section class="item card card--back">
  <div class="brand">Kjelvraket</div>
  <div class="card-web">www.fjordlast.no</div>
</section>

<!-- Business card back, dark -->
<section class="item card card--dark">
  <div class="brand">Kjelvraket</div>
  <div class="card-web">www.fjordlast.no</div>
</section>

<!-- Parcel sticker, rectangular -->
<section class="item sticker-rect">
  <svg class="wave" height="26"><use href="#swoosh"/></svg>
  <div class="sticker-meta">Fjordlast.no/tilbakemelding<br>phone : 47 382 066</div>
  <div class="brand">Kjelvraket</div>
  <p class="sticker-text">Tekst and link<br>Fraktae av Kjelvraket<br>Ke du syns?</p>
</section>

<!-- Parcel sticker, round -->
<section class="item sticker-round">
  <svg class="wave" height="30"><use href="#swoosh"/></svg>
  <div class="brand">Kjelvraket</div>
  <p class="sticker-text">Tekst and link<br>Fraktae av Kjelvraket<br>Ke du syns?</p>
  <p class="sticker-small">Fjordlast.no/tilbakemelding<br>phone : 47 382 066</p>
</section>

</body>
</html>
```